Animal Eye Clinic needs a Business card

We are a new veterinary ophthalmology practice (Ridgeline Pet Vision Care) and we need a business card designed. We only see animal eyes - we are not a regular veterinary clinic. We already have a logo. We are looking for a professional, good looking business card to hand out to our clients. We are looking for something simple but professional and contemporary. Our logo is likely the only picture/graphic that needs to be on the card.
Updates

Contact Information for Business Card

Delia Vossman, BSc, DVM, MSc, DipACVO
Veterinary Ophthalmologist

Phone: 250.418.3927
Email: ridgelinepetvisioncare@mailbox-example.net
Website: ridgelinepetvisioncare-example.net
Address: 1874 Thornbury Rd
Kelowna, BC, V1X 4M9

Colors

Designer to choose colors to be used in the design.

Requirements
Must have
• Our logo (attached)

```html
<!DOCTYPE html>
<html lang="en">
<head>
<meta charset="utf-8">
<title>Ridgeline Pet Vision Care — Business Card</title>
<link rel="stylesheet" href="https://fonts.googleapis.com/css2?family=Roboto:wght@400;500&display=swap">
<style>
  :root {
    --backdrop: #1c1c1c;
    --card-dark: #1f1f1f;
    --card-light: #ffffff;
    --teal: #0a95a8;
    --ink: #666666;
    --ink-soft: #777777;
  }
  * { box-sizing: border-box; margin: 0; padding: 0; }
  html, body { width: 1200px; height: 900px; overflow: hidden; }
  body {
    background: var(--backdrop);
    font-family: "Roboto", Arial, sans-serif;
    position: relative;
  }
  .card {
    position: absolute;
    left: 250px;
    width: 700px;
    height: 400px;
    overflow: hidden;
  }
  .card--front { top: 40px; background: var(--card-dark); }
  .card--back { top: 460px; background: var(--card-light); }

  /* Front */
  .brand {
    position: absolute;
    inset: 0;
    display: flex;
    align-items: center;
    justify-content: center;
    gap: 18px;
  }
  .brand__dot {
    width: 44px; height: 44px;
    border-radius: 50%;
    background: var(--teal);
  }
  .brand__name {
    color: var(--teal);
    font-weight: 500;
    font-size: 30px;
    letter-spacing: 1px;
    text-transform: uppercase;
    line-height: 1.1;
  }
  .brand__name span { display: block; letter-spacing: 11px; font-size: 18px; }

  /* Back */
  .person { position: absolute; left: 40px; top: 34px; }
  .person__bar {
    position: absolute; left: -40px; top: 6px;
    width: 12px; height: 30px; background: var(--teal);
  }
  .person__name { color: var(--teal); font-weight: 400; font-size: 36px; line-height: 1.1; }
  .person__creds, .person__role { color: var(--ink); font-size: 16px; line-height: 1.35; }

  .contact { position: absolute; left: 40px; bottom: 34px; color: var(--ink-soft); font-size: 17px; }
  .contact__address { font-size: 19px; line-height: 1.3; margin-bottom: 14px; }
  .contact__row { display: flex; align-items: center; gap: 10px; line-height: 1.55; }
  .contact__row svg { width: 15px; height: 15px; flex: none; }
  .contact__web strong { font-weight: 500; }

  .mark-area {
    position: absolute;
    right: 0; top: 120px;
    width: 270px; height: 280px;
    background: linear-gradient(160deg, #0fa3b6, #08879a);
    border-top-left-radius: 140px;
  }
</style>
</head>
<body>
  <section class="card card--front">
    <div class="brand">
      <div class="brand__dot"></div>
      <div class="brand__name"><span>Ridgeline</span>Pet Vision Care</div>
    </div>
  </section>

  <section class="card card--back">
    <div class="person">
      <div class="person__bar"></div>
      <h1 class="person__name">Delia Vossman</h1>
      <p class="person__creds">BSc, DVM, MSc, DipACVO</p>
      <p class="person__role">Veterinary Ophthalmologist</p>
    </div>

    <div class="contact">
      <p class="contact__address">Address: 1874 Thornbury Rd<br>Kelowna, BC, V1X 4M9</p>
      <p class="contact__row">
        <svg viewBox="0 0 16 16" aria-hidden="true"><path d="M4 1.5l2.2 3-1.3 1.6c.8 1.9 2.3 3.4 4.2 4.2l1.6-1.3 3 2.2-1.2 2.6C7.5 13.6 2.4 8.5 1.5 3z" fill="var(--teal)"/></svg>
        250.418.3927
      </p>
      <p class="contact__row">
        <svg viewBox="0 0 16 16" aria-hidden="true"><rect x="1.5" y="3.5" width="13" height="9" fill="none" stroke="var(--teal)" stroke-width="1.4"/><path d="M1.5 3.5L8 9l6.5-5.5" fill="none" stroke="var(--teal)" stroke-width="1.4"/></svg>
        ridgelinepetvisioncare@mailbox-example.net
      </p>
      <p class="contact__row contact__web">
        <svg viewBox="0 0 16 16" aria-hidden="true"><g fill="none" stroke="var(--teal)" stroke-width="1.2"><circle cx="8" cy="8" r="6.5"/><ellipse cx="8" cy="8" rx="2.8" ry="6.5"/><path d="M1.5 8h13M2.5 4.8h11M2.5 11.2h11"/></g></svg>
        <span>www.<strong>ridgelinepetvisioncare-example</strong>.net</span>
      </p>
    </div>

    <div class="mark-area" role="img" aria-label="Large practice emblem decoration in teal"></div>
  </section>
</body>
</html>
```